Business Card Design for Marketing Firm

Looking for business card design for higher end marketing firm. Clean but impressionable/trendy. We are a marketing firm that represents manufacturers in the foodservice equipment and supply industry. Our customers are end users such has hotels, restaurants, country clubs, convention centers and casinos as well as distributors of restaurants supplies and equipment, and manufacturers of foodservice equipment and supplies.
Target Market(s)
Hotels, Restaurants, Supply & Equipment Distributors, Foodservice Manufacturers
Industry/Entity Type
Foodservice/Hospitality
Contact Information for Business Card
Name, Title, Contact Number, Email, Website, Social Media, Address
Requirements
Must have
- Clean & Simple but Serious and Impressionable

```html
<!DOCTYPE html>
<html lang="en">
<head>
<meta charset="utf-8">
<title>Business Card – Meridian Service Reps</title>
<link rel="stylesheet" href="https://fonts.googleapis.com/css2?family=Montserrat:wght@400;500;600&display=swap">
<style>
  :root {
    --navy: #0b0a82;
    --ink-grey: #6d6d72;
    --paper: #ffffff;
    --backdrop: #e6e6ea;
    --card-shadow: rgba(20, 20, 40, 0.18);
  }
  * { margin: 0; padding: 0; box-sizing: border-box; }
  html, body {
    width: 1200px;
    height: 987px;
    overflow: hidden;
    background: var(--backdrop);
    font-family: "Montserrat", sans-serif;
  }
  .canvas {
    position: relative;
    width: 1200px;
    height: 987px;
  }
  .card {
    position: absolute;
    left: 300px;
    width: 600px;
    height: 343px;
    box-shadow: 0 10px 30px var(--card-shadow);
  }
  /* Back side */
  .card--back {
    top: 110px;
    background: var(--navy);
    color: var(--paper);
    display: flex;
    flex-direction: column;
    align-items: center;
  }
  .card--back .brand {
    margin-top: 120px;
    display: flex;
    align-items: center;
    gap: 12px;
    font-size: 30px;
    font-weight: 500;
    letter-spacing: 0.06em;
  }
  .card--back .brand-dot {
    width: 14px; height: 14px;
    border-radius: 50%;
    background: var(--paper);
  }
  .card--back .tagline {
    margin-top: auto;
    margin-bottom: 50px;
    font-size: 15px;
    letter-spacing: 0.02em;
  }
  /* Front side */
  .card--front {
    top: 534px;
    background: var(--paper);
  }
  .front-brand {
    position: absolute;
    right: 46px;
    top: 64px;
    display: flex;
    align-items: center;
    gap: 10px;
    color: var(--navy);
    font-size: 19px;
    font-weight: 500;
    letter-spacing: 0.05em;
    padding-bottom: 8px;
    border-bottom: 1.5px solid var(--navy);
  }
  .front-brand .brand-dot {
    width: 10px; height: 10px;
    border-radius: 50%;
    background: var(--navy);
  }
  .divider {
    position: absolute;
    left: 48px;
    right: 46px;
    top: 170px;
    border-top: 1.5px solid var(--navy);
  }
  .person {
    position: absolute;
    left: 48px;
    top: 118px;
  }
  .person-name {
    color: var(--navy);
    font-size: 24px;
    font-weight: 600;
    line-height: 1.05;
  }
  .person-title {
    color: var(--ink-grey);
    font-size: 16px;
    line-height: 1.2;
  }
  .contacts {
    position: absolute;
    left: 48px;
    top: 190px;
    list-style: none;
    color: var(--ink-grey);
    font-size: 17px;
    line-height: 25px;
  }
  .contacts li {
    display: flex;
    align-items: center;
    gap: 9px;
  }
  .contacts svg { width: 15px; height: 15px; fill: var(--navy); flex: none; }
  .social-mark {
    width: 14px; height: 14px;
    background: var(--navy);
    flex: none;
    margin-left: 1px;
  }
  .address {
    position: absolute;
    right: 46px;
    top: 200px;
    text-align: right;
    color: var(--ink-grey);
    font-size: 16px;
    line-height: 23px;
  }
</style>
</head>
<body>
<main class="canvas">

  <section class="card card--back" aria-label="Business card back">
    <div class="brand"><span class="brand-dot"></span>MERIDIAN</div>
    <p class="tagline">Your tag line goes here</p>
  </section>

  <section class="card card--front" aria-label="Business card front">
    <div class="front-brand"><span class="brand-dot"></span>MERIDIAN SERVICE REPS</div>

    <div class="person">
      <p class="person-name">John Smith</p>
      <p class="person-title">President</p>
    </div>

    <div class="divider"></div>

    <ul class="contacts">
      <li>
        <svg viewBox="0 0 24 24" aria-hidden="true"><path d="M6.6 10.8a15.1 15.1 0 0 0 6.6 6.6l2.2-2.2a1 1 0 0 1 1-.25 11.4 11.4 0 0 0 3.6.57 1 1 0 0 1 1 1V20a1 1 0 0 1-1 1A17 17 0 0 1 3 4a1 1 0 0 1 1-1h3.5a1 1 0 0 1 1 1c0 1.25.2 2.45.57 3.57a1 1 0 0 1-.25 1z"/></svg>
        012-345-6789
      </li>
      <li><span class="social-mark"></span>/yourfacebookhere</li>
      <li>
        <svg viewBox="0 0 24 24" aria-hidden="true"><path d="M2 5h20v14H2z M2 5l10 8 10-8" fill="none" stroke="#0b0a82" stroke-width="0"/><path d="M2 5h20l-10 8z"/><path d="M2 7.5l10 8 10-8V19H2z"/></svg>
        info@yourwebsitehere.com
      </li>
      <li>
        <svg viewBox="0 0 24 24" aria-hidden="true"><circle cx="12" cy="12" r="9.5" fill="none" stroke="#0b0a82" stroke-width="2"/><ellipse cx="12" cy="12" rx="4" ry="9.5" fill="none" stroke="#0b0a82" stroke-width="1.6"/><path d="M2.5 12h19M4 7h16M4 17h16" stroke="#0b0a82" stroke-width="1.6"/></svg>
        yourwebsitehere.com
      </li>
    </ul>

    <address class="address" style="font-style:normal">
      Street Name, Suite 100<br>
      State, Zip Code, Country
    </address>
  </section>

</main>
</body>
</html>
```